Communication and Marketing agency needs a new presentation card

We are a group of communication and marketing agencies specialized in companies that are in the logistics and industrial sector. The head agency is TELVANO Grupo and the group consists of 4 agencies: TELVANO Media, TELVANO Digital, TELVANO Research and DifundeEnPantalla. We hace 4 offices in Spain (Madrid, Barcelona, Valencia and Murcia). We are looking for a clean and attractive design that transmits our experience, brand presence in the market and knowledge to those who receive the card.It has to maintain the colors of the logo that is attached.
Target Market(s)
logistics and industrial sector
Marketing department
Contact Information for Business Card
Clean and attractive design

```html
<!DOCTYPE html>
<html lang="en">
<head>
<meta charset="utf-8">
<title>TELVANO Grupo – Business Card</title>
<link rel="stylesheet" href="https://fonts.googleapis.com/css2?family=Montserrat:wght@300;400;600;700&display=swap">
<style>
  :root {
    --stage: #3f4042;
    --card-dark: #57575a;
    --card-light: #ffffff;
    --brand-red: #b8202e;
    --ink-grey: #555557;
    --rule-grey: #4a4a4c;
    --silver: #e6e6e8;
    --silver-soft: #bdbdc0;
  }
  * { box-sizing: border-box; margin: 0; padding: 0; }
  html, body { width: 1200px; height: 960px; overflow: hidden; }
  body {
    background: radial-gradient(circle at 50% 40%, #58595b 0%, var(--stage) 70%);
    font-family: "Montserrat", sans-serif;
    position: relative;
  }
  .card {
    position: absolute;
    left: 290px;
    width: 620px;
    height: 354px;
    box-shadow: 0 14px 30px rgba(0,0,0,.35);
  }
  /* Back side */
  .card--back {
    top: 90px;
    background: var(--card-dark);
    display: grid;
    grid-template-columns: 1fr 1fr;
    grid-template-rows: 1fr 1fr;
    padding: 90px 60px;
    align-items: center;
    justify-items: center;
  }
  .agency-name {
    font-weight: 600;
    font-size: 24px;
    letter-spacing: 1px;
    color: var(--silver);
  }
  .agency-name--muted { color: var(--silver-soft); }
  /* Front side */
  .card--front {
    top: 510px;
    background: var(--card-light);
  }
  .brand {
    position: absolute;
    right: 48px;
    top: 52px;
    font-weight: 400;
    font-size: 38px;
    letter-spacing: 2px;
    color: var(--brand-red);
  }
  .rule {
    position: absolute;
    top: 196px;
    height: 2px;
  }
  .rule--grey { left: 48px; width: 250px; background: var(--rule-grey); }
  .rule--red { left: 298px; width: 274px; background: var(--brand-red); }
  .person {
    position: absolute;
    left: 48px;
    top: 130px;
  }
  .person__name {
    font-weight: 700;
    font-size: 24px;
    color: var(--brand-red);
    line-height: 1.1;
  }
  .person__title {
    font-weight: 300;
    font-size: 18px;
    color: var(--ink-grey);
  }
  .contacts {
    position: absolute;
    left: 48px;
    top: 214px;
    list-style: none;
  }
  .contacts li {
    display: flex;
    align-items: center;
    gap: 12px;
    font-weight: 400;
    font-size: 17px;
    color: var(--ink-grey);
    line-height: 30px;
  }
  .contacts svg, .address svg { flex: none; }
  .address {
    position: absolute;
    left: 360px;
    top: 214px;
    display: flex;
    gap: 12px;
    align-items: flex-start;
    font-weight: 400;
    font-size: 17px;
    line-height: 24px;
    color: var(--ink-grey);
  }
</style>
</head>
<body>

  <section class="card card--back" aria-label="Card back with group agencies">
    <span class="agency-name agency-name--muted">TELVANO Media</span>
    <span class="agency-name">TELVANO Digital</span>
    <span class="agency-name agency-name--muted">TELVANO Research</span>
    <span class="agency-name">DifundeEnPantalla</span>
  </section>

  <section class="card card--front" aria-label="Card front with contact details">
    <div class="brand">TELVANO Grupo</div>

    <div class="person">
      <p class="person__name">Your Name</p>
      <p class="person__title">Your Title</p>
    </div>

    <div class="rule rule--grey"></div>
    <div class="rule rule--red"></div>

    <ul class="contacts">
      <li>
        <svg width="16" height="16" viewBox="0 0 24 24" aria-hidden="true"><path fill="#b8202e" d="M6.6 10.8a15.5 15.5 0 0 0 6.6 6.6l2.2-2.2c.3-.3.7-.4 1-.2 1.1.4 2.3.6 3.6.6.6 0 1 .4 1 1V20c0 .6-.4 1-1 1C10.6 21 3 13.4 3 4c0-.6.4-1 1-1h3.5c.6 0 1 .4 1 1 0 1.3.2 2.5.6 3.6.1.3 0 .7-.2 1z"/></svg>
        123-456-2100
      </li>
      <li>
        <svg width="16" height="16" viewBox="0 0 24 24" aria-hidden="true"><path fill="#b8202e" d="M2 5h20v14H2z"/><path fill="none" stroke="#fff" stroke-width="1.6" d="M2 5l10 8 10-8"/></svg>
        youremail@telvano.es
      </li>
      <li>
        <svg width="16" height="16" viewBox="0 0 24 24" aria-hidden="true"><circle cx="12" cy="12" r="10" fill="#b8202e"/><path fill="none" stroke="#fff" stroke-width="1.4" d="M2 12h20M12 2c3 3 3 17 0 20M12 2c-3 3-3 17 0 20"/></svg>
        www.yourwebsite.com
      </li>
    </ul>

    <div class="address">
      <svg width="16" height="22" viewBox="0 0 24 32" aria-hidden="true"><path fill="#b8202e" d="M12 0C5.4 0 0 5.2 0 11.7 0 20.5 12 32 12 32s12-11.5 12-20.3C24 5.2 18.6 0 12 0zm0 16a4.5 4.5 0 1 1 0-9 4.5 4.5 0 0 1 0 9z"/></svg>
      <p>Your address, city<br>state, ZIP 0000</p>
    </div>
  </section>

</body>
</html>
```